Logo and Card design for KRV Home Solutions LLC

I need an edgier logo and business card designs. Current logo attached. I like the colors below. I would like the logo to incorporate a home in the design.
Title = Principal-Acquisitions
Email:KRVHOMESOLUTIONS@fernmail.example
555-214-0937
facebook
IG
2 sided business card with the front being contact info a slogan about selling a home fast. The back incorporating What we do. Buy houses, land, or commercial property as is. We find solutions to make the process of selling simple and fair.

Target Market(s)

Motivated house sellers.

Industry/Entity Type

Business

Contact Information for Business Card

Who we are: We are a Faith based Real Estate Investment Company. We pay cash for homes in any condition and can close quick. Whatever the reason you need to sell fast, we can help. We believe in creating win-win solutions to help you in your time of need. We care! We can help!

Logo Text

KRV Home Solutions LLC

Font styles to use
Sans Serif

Colors
33a6d7
0355a3
85abd2
cee9f5
9d9d9d
b2b2b2
ffffff

Requirements
Must have
• Old logo attached. I want something edgier.
• Company name, phone number, description on the back of what we can do. Pay all cash. Buy in as is condition. No fees,Commisions or closing costs.Close quick. No hassles with solutions to meet your unique situation.
• Call today for an offer within 24 hours.

```html
<!DOCTYPE html>
<html lang="en">
<head>
<meta charset="utf-8">
<title>KRV Home Solutions – Business Card</title>
<link rel="stylesheet" href="https://fonts.googleapis.com/css2?family=Roboto:wght@400;500;700&display=swap">
<style>
  :root {
    --page-bg: #e9e9e7;
    --navy: #1d3a86;
    --navy-deep: #16306f;
    --panel-grey: #5a5d58;
    --photo-light: #eef0ea;
    --photo-mid: #c9d3bf;
    --brand-blue: #0355a3;
    --slate: #3c4457;
    --white: #ffffff;
    --text-soft: #e6e8ec;
  }
  * { box-sizing: border-box; margin: 0; padding: 0; }
  html, body {
    width: 1200px; height: 886px; overflow: hidden;
    background: var(--page-bg);
    font-family: "Roboto", Arial, sans-serif;
  }
  .sheet {
    position: relative; width: 1200px; height: 886px;
    display: flex; align-items: center; justify-content: center; gap: 40px;
  }
  .card {
    position: relative; width: 540px; height: 309px;
    overflow: hidden; border-radius: 3px;
    box-shadow: 0 10px 28px rgba(0,0,0,.18);
  }

  /* Front */
  .card-front { background: var(--photo-light); }
  .front-photo {
    position: absolute; inset: 0;
    background: linear-gradient(160deg, var(--photo-light) 0%, #dde3d6 45%, var(--photo-mid) 100%);
  }
  .front-panel { position: absolute; inset: 0; }
  .front-brand {
    position: absolute; left: 34px; bottom: 46px;
    display: flex; align-items: center; gap: 10px;
    color: var(--slate); font-weight: 700; font-size: 24px; letter-spacing: .5px;
  }
  .front-brand .mark {
    width: 18px; height: 18px; background: var(--brand-blue);
  }
  .front-info {
    position: absolute; right: 26px; top: 26px; width: 290px;
    color: var(--white); text-align: right;
  }
  .person-name { font-size: 19px; font-weight: 700; letter-spacing: .4px; }
  .person-title { font-size: 12px; margin-top: 3px; color: var(--text-soft); }
  .contact-list { list-style: none; margin-top: 14px; font-size: 10.5px; line-height: 1.7; }
  .contact-list li { display: flex; justify-content: flex-end; align-items: center; gap: 7px; }
  .contact-list svg { width: 11px; height: 11px; flex: none; }
  .offer-list { list-style: none; margin-top: 12px; font-size: 10.5px; line-height: 1.55; }
  .offer-list li { display: flex; justify-content: flex-end; align-items: center; gap: 8px; }
  .offer-list li::after {
    content: ""; width: 4px; height: 4px; border-radius: 50%;
    background: var(--white); flex: none;
  }

  /* Back */
  .card-back {
    background: linear-gradient(150deg, var(--navy) 0%, var(--navy-deep) 100%);
    color: var(--white); text-align: center;
    padding: 30px 40px 0;
  }
  .back-brand {
    display: inline-flex; align-items: center; gap: 10px;
    font-size: 24px; font-weight: 700; letter-spacing: .5px;
  }
  .back-brand .mark { width: 18px; height: 18px; background: var(--white); }
  .section-title {
    font-size: 12px; font-weight: 700; letter-spacing: .6px; margin-top: 18px;
  }
  .section-text { font-size: 10.5px; line-height: 1.5; margin-top: 6px; color: var(--text-soft); }
</style>
</head>
<body>
<main class="sheet">

  <section class="card card-front" aria-label="Business card front">
    <div class="front-photo" role="img" aria-label="Photo of a two-storey family house with green lawn, faded to white"></div>
    <svg class="front-panel" viewBox="0 0 540 309" preserveAspectRatio="none" aria-hidden="true">
      <polygon points="300,0 540,0 540,309 195,309" fill="var(--panel-grey)" opacity=".92"/>
    </svg>
    <div class="front-brand"><span class="mark"></span>KRV Home Solutions</div>
    <div class="front-info">
      <h1 class="person-name">ALEX MORGAN</h1>
      <p class="person-title">Principal-Acquisitions</p>
      <ul class="contact-list">
        <li>555-214-0937
          <svg viewBox="0 0 24 24"><path fill="#fff" d="M6.6 10.8a15 15 0 0 0 6.6 6.6l2.2-2.2c.3-.3.7-.4 1-.2 1.1.4 2.3.6 3.6.6.6 0 1 .4 1 1V20c0 .6-.4 1-1 1A17 17 0 0 1 3 4c0-.6.4-1 1-1h3.5c.6 0 1 .4 1 1 0 1.3.2 2.5.6 3.6.1.3 0 .7-.2 1z"/></svg>
        </li>
        <li>KRVHOMESOLUTIONS@fernmail.example
          <svg viewBox="0 0 24 24"><rect x="2" y="5" width="20" height="14" rx="1.5" fill="#fff"/><path d="M3 6l9 7 9-7" stroke="var(--panel-grey)" stroke-width="2" fill="none"/></svg>
        </li>
        <li>KRVHOMESOLUTIONS.example
          <svg viewBox="0 0 24 24"><circle cx="12" cy="12" r="9" fill="none" stroke="#fff" stroke-width="2"/><path d="M3 12h18M12 3c3 3 3 15 0 18M12 3c-3 3-3 15 0 18" stroke="#fff" stroke-width="1.6" fill="none"/></svg>
        </li>
      </ul>
      <ul class="offer-list">
        <li>Pay all cash. Buy in as is condition</li>
        <li>No fees,Commisions or closing costs</li>
        <li>Close quick. No hassles with</li>
        <li>solutions to meet your unique situation</li>
        <li>Call today for an offer within 24 hours</li>
      </ul>
    </div>
  </section>

  <section class="card card-back" aria-label="Business card back">
    <div class="back-brand"><span class="mark"></span>KRV Home Solutions</div>
    <h2 class="section-title">WHO WE ARE</h2>
    <p class="section-text">We are a Faith based Real Estate Investment Company. We pay cash for homes in any condition and can close quick. Whatever the reason you need to sell fast, we can help. We believe in creating win-win solutions to help you in your time of need.</p>
    <h2 class="section-title">WHAT WE DO</h2>
    <p class="section-text">Buy houses, land, or commercial property as is.<br>We find solutions to make the process of selling simple and fair.</p>
  </section>

</main>
</body>
</html>
```